Business card design for new eCommerce site focusing on integrity and strong businsess tactics

We need a business card that will stand out and be memorable. Something with color that matches our company logo colors. Think high end version of Pactivo. There are 2 logos provided. The parent company is called Amber Ledge Partners and we are presenting a new and very exciting eCommerce site called BrightHarborTrade.example.

Target Market(s)

Our target markets are in the Activities, Food and Beverage, Health and Beauty

Industry/Entity Type

Marketing

Contact Information for Business Card

We have 4 members that need cards...I will provide all info to the winner of the design contest
Business Address is
4870 West 63rd Avenue, Suite C207
Phoenix AZ 85731

Font styles to use
Serif
Sans Serif

Colors

Designer to choose colors to be used in the design.

Requirements
Must have
• The card must be memorable...should be unique in design but must exude integrity and be playful .
• I have provided several colors or our parent company...please feel free to use which ever
Nice to have
• I will leave this up to you. Feel free to use other images of your choosing that wraps around our client.....Activities, Dining, Health, Beauty
Should not have
• just dont be boring

```html
<!DOCTYPE html>
<html lang="en">
<head>
<meta charset="utf-8">
<title>Amber Ledge Partners – Business Cards</title>
<link href="https://fonts.googleapis.com/css2?family=Roboto:wght@400;500;700&family=Roboto+Condensed:wght@700&display=swap" rel="stylesheet">
<style>
  :root {
    --backdrop: #2b2b2c;
    --card-dark: #1c1d1f;
    --card-light: #f2f2f2;
    --brand-green: #a3c83e;
    --brand-blue: #2b7fb6;
    --text-grey: #555a5e;
  }
  * { margin: 0; padding: 0; box-sizing: border-box; }
  html, body { width: 1200px; height: 960px; overflow: hidden; }
  body {
    background: var(--backdrop);
    position: relative;
    font-family: "Roboto", Arial, sans-serif;
  }
  .card {
    position: absolute;
    width: 600px;
    height: 342px;
    border-radius: 22px;
    overflow: hidden;
  }
  .card-back {
    left: 322px; top: 110px;
    background: var(--card-dark);
  }
  .card-front {
    left: 320px; top: 493px;
    background: var(--card-light);
  }
  /* back side */
  .brand-disc {
    position: absolute;
    left: 228px; top: 68px;
    width: 144px; height: 144px;
    border-radius: 50%;
    background: var(--brand-green);
    box-shadow: 0 0 0 4px var(--card-dark), 0 0 0 6px var(--brand-green);
  }
  .brand-name {
    position: absolute;
    left: 0; right: 0; top: 222px;
    text-align: center;
    color: var(--brand-green);
    font-weight: 700;
    font-size: 34px;
    letter-spacing: -0.3px;
  }
  /* front side */
  .accent-panel {
    position: absolute;
    left: 0; top: 0;
    width: 240px; height: 342px;
  }
  .site-name {
    position: absolute;
    right: 40px; top: 46px;
    color: var(--brand-blue);
    font-weight: 500;
    font-size: 20px;
  }
  .site-tagline {
    position: absolute;
    right: 40px; top: 76px;
    color: var(--text-grey);
    font-size: 11px;
    letter-spacing: 0.8px;
  }
  .person {
    position: absolute;
    right: 40px; top: 136px;
    text-align: right;
  }
  .person-name {
    font-family: "Roboto Condensed", "Roboto", sans-serif;
    font-weight: 700;
    font-size: 22px;
    color: var(--brand-blue);
    line-height: 1.1;
  }
  .person-role {
    font-weight: 500;
    font-size: 14px;
    color: var(--brand-green);
    margin-top: 3px;
  }
  .address {
    position: absolute;
    right: 40px; top: 190px;
    text-align: right;
    font-size: 14px;
    line-height: 19px;
    color: var(--text-grey);
  }
  .contact-list {
    position: absolute;
    right: 40px; top: 235px;
    list-style: none;
    font-size: 14px;
    line-height: 19.5px;
    color: var(--text-grey);
    text-align: right;
  }
  .contact-list li { display: flex; justify-content: flex-end; align-items: center; gap: 8px; }
  .contact-icon { width: 12px; height: 12px; flex: none; }
</style>
</head>
<body>

<section class="card card-back" aria-label="Card back">
  <div class="brand-disc"></div>
  <div class="brand-name">Amber Ledge Partners</div>
</section>

<section class="card card-front" aria-label="Card front">
  <svg class="accent-panel" viewBox="0 0 240 342" aria-hidden="true">
    <path d="M0 0 H140 C200 40 235 110 215 170 C195 240 120 280 140 342 H0 Z" fill="var(--brand-blue)"/>
  </svg>

  <div class="site-name">BrightHarborTrade.example</div>
  <div class="site-tagline">Activities-Dining-Health-Beauty</div>

  <div class="person">
    <div class="person-name">DANA WHITFIELD</div>
    <div class="person-role">CEO/FOUNDER</div>
  </div>

  <div class="address">
    4870 West 63rd Avenue<br>
    Suite C207, Phoenix AZ 85731
  </div>

  <ul class="contact-list">
    <li>602 555 0147
      <svg class="contact-icon" viewBox="0 0 12 12"><path d="M2.5 1 L4.5 1 L5.3 3.6 L4 4.6 Q5 7 7.4 8 L8.4 6.7 L11 7.5 L11 9.5 Q10.5 11 9 11 Q1 10 1 2.8 Q1 1.3 2.5 1 Z" fill="var(--brand-blue)"/></svg>
    </li>
    <li>602 555 0193
      <svg class="contact-icon" viewBox="0 0 12 12"><rect x="3" y="0.5" width="6.5" height="11" rx="1" fill="none" stroke="var(--brand-blue)" stroke-width="1.3"/><circle cx="6.25" cy="9.6" r="0.7" fill="var(--brand-blue)"/></svg>
    </li>
    <li>dana@brightharbortrade.example
      <svg class="contact-icon" viewBox="0 0 12 12"><rect x="0.5" y="2.5" width="11" height="7.5" fill="var(--brand-blue)"/><path d="M0.8 2.8 L6 7 L11.2 2.8" fill="none" stroke="var(--card-light)" stroke-width="1"/></svg>
    </li>
    <li>www.brightharbortrade.example
      <svg class="contact-icon" viewBox="0 0 12 12"><circle cx="6" cy="6" r="5.5" fill="var(--brand-blue)"/><path d="M1 6 H11 M6 0.5 Q3 6 6 11.5 M6 0.5 Q9 6 6 11.5" fill="none" stroke="var(--card-light)" stroke-width="0.8"/></svg>
    </li>
  </ul>
</section>

</body>
</html>
```